Paper Promise website home page slider banner assets

Background; I am building a website by the name of Paper Promise on Wordpress, using the Loresh responsive theme. The site will include eCommerce functionality, selling gifts and gift certificates/coupons - refer to file attached to this brief 'Coupon Template' for sample. I am aiming for a modern look and feel and have a preference for a 'retro' colour scheme (see Must Haves for colour palette) & refer to 'Logo tagline' attachment for sample.
I am moving away from using standard readily-available stock images, so am looking for original, creative content with an edge..

This spec is for a a set of 3 banner assets (background and associated images) to be used on the main slider of my site. Banners should be based on the attached images, but I would like to see some original work, as I'm trying to move away from using stock images for this project.

Banner Specs:

Banner #1:
- 2 assets required, to be based on attached file 'HotAirBalloon.png'. Require a separate background file and hot air balloon image.
- Background image dimensions 1280 (W) X 720 (H) pixels. Background to be based on 'HotAirBalloon.png' image background (cloudy sky) with the same look and feel.
- Hot air balloon image dimensions to be proportional to background; designer to determine suitable size. Image should be based on image in 'Slide', including the rainbow trail.

Banner #2:
- 3 assets required, to be based on attached files. Require a separate background file and 2Xowl images.
- Background image dimensions 1280 (W) X 720 (H) pixels. I have attached a range of samples of preferred styles to provide inspiration to designers.
- Other image dimensions to be proportional to background; designer to determine suitable size. Require 2 X owl images using project colour palette (see Must Haves); one owl to be in perched position, and one in flight (illustrations or photos can be used).

Banner #3:
- 3-4 assets required, to be based on attached files. Require a separate background file and 1Xhourglass image and 2-3 clock/watch/watch face images.
- Other image dimensions to be proportional to background; designer to determine suitable size.
- Require 1 X hourglass image
- Require 2-3 X clock/watch/clock face images (illustrations or photos can be used).

NOTE: I have a PixelHarbor account.

Industry/Entity Type

Building

Font styles to use
Sans Serif

Requirements
Must have
• Below is the colour palette for this project:
• Main:
• Turquoise: #07B1BF
• Grey-Brown (Dark): #685662
• Grey-Brown (Light): #747173
• Gold-Brown: #94814B
• Complementary:
• Off-White & Grey Shades:
• #FEFEFE
• #EDF2F1
• Turquoise Shades:
• #ACDDE2
• #0BC8D9
• #63C2CD
• #06B1BF
• #00B0BE
• #05838D
• #015D64
• Beige Shades:
• #B8B1A7
• #AA9970
• #93804A
• #7A6A40
• Brown-Grey Shades:
• #D5D1CB
• #938E92
• #433C38
• #232120
• #0B0911

```html
<!DOCTYPE html>
<html lang="en">
<head>
<meta charset="utf-8">
<title>Paper Promise – Slider Banners</title>
<link rel="stylesheet" href="https://fonts.googleapis.com/css2?family=Alfa+Slab+One&family=Great+Vibes&display=swap">
<style>
  :root {
    --page-bg: #ecebe8;
    --turquoise: #07b1bf;
    --turquoise-bright: #0bc8d9;
    --turquoise-soft: #acdde2;
    --turquoise-mid: #63c2cd;
    --turquoise-deep: #05838d;
    --greybrown-dark: #685662;
    --greybrown-light: #938e92;
    --gold: #94814b;
    --beige: #aa9970;
    --beige-light: #d5d1cb;
    --paper: #e7e4df;
    --offwhite: #edf2f1;
  }
  * { box-sizing: border-box; margin: 0; padding: 0; }
  html, body {
    width: 1200px;
    height: 1200px;
    overflow: hidden;
    background: var(--page-bg);
  }
  .canvas {
    position: relative;
    width: 1200px;
    height: 1200px;
  }
  .banner {
    position: absolute;
    left: 176px;
    width: 848px;
    height: 478px;
    overflow: hidden;
  }
  .banner--sky { top: 60px; background: var(--turquoise-soft); }
  .banner--paper { top: 662px; background: var(--paper); }

  .cloud-layer {
    position: absolute;
    inset: 0;
  }
  .banner--sky .cloud-layer {
    background: radial-gradient(ellipse at 70% 30%, #c9eef2 0%, #9fdce5 45%, #8fd4df 100%);
  }
  .banner--paper .cloud-layer {
    background: radial-gradient(ellipse at 70% 35%, #e3f1f1 0%, #e4e1dc 55%, #e7e4df 100%);
  }

  .trail {
    position: absolute;
    inset: 0;
    width: 848px;
    height: 478px;
  }
  .banner--sky .band-1 { fill: var(--beige-light); }
  .banner--sky .band-2 { fill: #3e9fa8; }
  .banner--sky .band-3 { fill: var(--gold); }
  .banner--sky .band-4 { fill: var(--greybrown-dark); }
  .banner--paper .band-1 { fill: var(--turquoise-bright); }
  .banner--paper .band-2 { fill: var(--beige); }
  .banner--paper .band-3 { fill: var(--beige-light); }
  .banner--paper .band-4 { fill: var(--greybrown-light); }

  .balloon {
    position: absolute;
    left: 52px;
    top: 12px;
    width: 250px;
    height: 395px;
  }

  .brand {
    position: absolute;
    left: 480px;
    top: 52px;
    width: 330px;
    text-align: center;
  }
  .brand__name {
    font-family: "Alfa Slab One", Georgia, serif;
    font-size: 36px;
    line-height: 48px;
    letter-spacing: 0.5px;
    color: var(--greybrown-dark);
  }
  .brand__tagline {
    margin-top: 44px;
    font-family: "Great Vibes", cursive;
    font-size: 40px;
    line-height: 44px;
    color: var(--greybrown-dark);
  }
</style>
</head>
<body>
<main class="canvas">

  <section class="banner banner--sky">
    <div class="cloud-layer" role="img" aria-label="Hand-drawn white sketched clouds on a textured turquoise sky"></div>
    <svg class="trail" viewBox="0 0 848 478" aria-hidden="true">
      <path class="band-1" d="M240 384 C360 300 460 262 560 282 C660 300 720 350 848 300 L848 344 C720 386 660 336 560 318 C460 292 360 314 240 384 Z"/>
      <path class="band-2" d="M240 384 C360 314 460 292 560 318 C660 336 720 386 848 344 L848 388 C720 422 660 372 560 354 C460 322 360 328 240 384 Z"/>
      <path class="band-3" d="M240 384 C360 328 460 322 560 354 C660 372 720 422 848 388 L848 432 C720 458 660 408 560 390 C460 352 360 342 240 384 Z"/>
      <path class="band-4" d="M240 384 C360 342 460 352 560 390 C660 408 720 458 848 432 L848 478 L700 478 C660 444 620 430 560 426 C460 382 360 356 240 384 Z"/>
    </svg>
    <svg class="balloon" viewBox="0 0 250 395" role="img" aria-label="Sketched vintage hot air balloon in pale grey with a dark basket">
      <defs>
        <radialGradient id="balloon-sky" cx="40%" cy="35%" r="70%">
          <stop offset="0%" stop-color="#f1efec"/>
          <stop offset="100%" stop-color="#d5d1cb"/>
        </radialGradient>
      </defs>
      <ellipse cx="125" cy="160" rx="125" ry="160" fill="url(#balloon-sky)"/>
    </svg>
    <div class="brand">
      <div class="brand__name">Paper Promise</div>
      <div class="brand__tagline">Make Today Count</div>
    </div>
  </section>

  <section class="banner banner--paper">
    <div class="cloud-layer" role="img" aria-label="Hand-drawn turquoise sketched clouds on a textured off-white paper background"></div>
    <svg class="trail" viewBox="0 0 848 478" aria-hidden="true">
      <path class="band-1" d="M240 384 C360 300 460 262 560 282 C660 300 720 350 848 300 L848 344 C720 386 660 336 560 318 C460 292 360 314 240 384 Z"/>
      <path class="band-2" d="M240 384 C360 314 460 292 560 318 C660 336 720 386 848 344 L848 388 C720 422 660 372 560 354 C460 322 360 328 240 384 Z"/>
      <path class="band-3" d="M240 384 C360 328 460 322 560 354 C660 372 720 422 848 388 L848 432 C720 458 660 408 560 390 C460 352 360 342 240 384 Z"/>
      <path class="band-4" d="M240 384 C360 342 460 352 560 390 C660 408 720 458 848 432 L848 478 L700 478 C660 444 620 430 560 426 C460 382 360 356 240 384 Z"/>
    </svg>
    <svg class="balloon" viewBox="0 0 250 395" role="img" aria-label="Sketched vintage hot air balloon in grey-brown with a turquoise basket">
      <defs>
        <radialGradient id="balloon-paper" cx="40%" cy="35%" r="70%">
          <stop offset="0%" stop-color="#c2bcb3"/>
          <stop offset="100%" stop-color="#aaa398"/>
        </radialGradient>
      </defs>
      <ellipse cx="125" cy="160" rx="125" ry="160" fill="url(#balloon-paper)"/>
    </svg>
    <div class="brand">
      <div class="brand__name">Paper Promise</div>
      <div class="brand__tagline">Make Today Count</div>
    </div>
  </section>

</main>
</body>
</html>
```